New Business Card Design Project

Need a design that will create an impact / strong impression towards our clients for our business. We are in the lighting business and we do lighting retrofits for large commercial to industrial clientele.

Target Market(s)

Lighting Industry

Industry/Entity Type

Business

Font styles to use
Other font styles liked:
• we would like to use the font on our logo, not sure what it is though..

Requirements
Must have
• Our logo.
Nice to have
• We are open to suggestions that have to do with lighting.

```html
<!DOCTYPE html>
<html lang="en">
<head>
<meta charset="utf-8">
<title>Kestrel Retrofits – Business Card</title>
<link rel="stylesheet" href="https://fonts.googleapis.com/css2?family=Lato:wght@400;700&family=Montserrat:wght@800&display=swap">
<style>
  :root {
    --bg: #3a3a3a;
    --green: #0a8237;
    --green-dark: #0f4a1c;
    --white: #ffffff;
    --ink: #1a1a1a;
  }
  html, body {
    margin: 0;
    padding: 0;
    width: 1200px;
    height: 900px;
    overflow: hidden;
    background: var(--bg);
    font-family: "Lato", Arial, sans-serif;
  }
  .card {
    position: absolute;
    left: 250px;
    width: 700px;
    height: 400px;
    overflow: hidden;
  }
  .card--back {
    top: 30px;
    background: var(--green);
  }
  .card--front {
    top: 470px;
    background: var(--white);
  }
  .brand {
    position: absolute;
    display: flex;
    align-items: center;
    gap: 14px;
    font-family: "Montserrat", Arial, sans-serif;
    font-weight: 800;
    letter-spacing: 1px;
    line-height: 1;
  }
  .brand__mark {
    display: block;
    flex: none;
  }
  .card--back .brand {
    left: 0;
    right: 0;
    top: 140px;
    justify-content: center;
    font-size: 62px;
    color: var(--white);
  }
  .card--back .brand__mark {
    width: 34px;
    height: 34px;
    background: var(--white);
  }
  .card--back .website {
    position: absolute;
    left: 0;
    right: 0;
    bottom: 48px;
    text-align: center;
    color: var(--white);
    font-size: 19px;
    letter-spacing: 1px;
  }
  .card--front .brand {
    left: 60px;
    top: 62px;
    font-size: 46px;
    color: var(--green-dark);
  }
  .card--front .brand__mark {
    width: 26px;
    height: 26px;
    background: var(--green-dark);
  }
  .person__name {
    position: absolute;
    right: 55px;
    top: 162px;
    font-size: 32px;
    font-weight: 700;
    color: var(--green);
    margin: 0;
    line-height: 1.1;
  }
  .divider {
    position: absolute;
    left: 0;
    top: 206px;
    width: 655px;
    height: 2px;
    background: var(--green);
  }
  .person__role {
    position: absolute;
    right: 55px;
    top: 212px;
    font-size: 21px;
    line-height: 26px;
    color: var(--ink);
    margin: 0;
  }
  .icon-tab {
    position: absolute;
    left: 0;
    top: 232px;
    width: 36px;
    height: 92px;
    background: var(--green-dark);
    border-radius: 0 6px 6px 0;
    display: flex;
    flex-direction: column;
    justify-content: space-around;
    align-items: center;
    padding: 4px 0;
    box-sizing: border-box;
  }
  .contact {
    position: absolute;
    left: 52px;
    top: 236px;
    margin: 0;
    padding: 0;
    list-style: none;
    font-size: 21px;
    line-height: 28px;
    color: var(--ink);
  }
  .address {
    position: absolute;
    right: 60px;
    top: 264px;
    text-align: right;
    font-size: 21px;
    line-height: 28px;
    color: var(--ink);
    font-style: normal;
  }
  .footer-band {
    position: absolute;
    left: 0;
    bottom: 0;
    width: 700px;
    height: 80px;
  }
  .footer-band .website {
    position: absolute;
    left: 300px;
    width: 350px;
    top: 30px;
    text-align: center;
    color: var(--white);
    font-size: 22px;
    letter-spacing: 0.5px;
  }
</style>
</head>
<body>

<section class="card card--back">
  <div class="brand"><span class="brand__mark"></span>Kestrel</div>
  <div class="website">www.kestrel-retrofits.com</div>
</section>

<section class="card card--front">
  <div class="brand"><span class="brand__mark"></span>Kestrel Retrofits</div>

  <p class="person__name">Marcus Hale</p>
  <div class="divider"></div>
  <p class="person__role">Manager</p>

  <div class="icon-tab">
    <svg width="16" height="16" viewBox="0 0 24 24" aria-label="Phone"><path fill="#fff" d="M6.6 10.8a15.1 15.1 0 0 0 6.6 6.6l2.2-2.2a1 1 0 0 1 1-.25 11.4 11.4 0 0 0 3.6.57 1 1 0 0 1 1 1V20a1 1 0 0 1-1 1A17 17 0 0 1 3 4a1 1 0 0 1 1-1h3.5a1 1 0 0 1 1 1c0 1.250.2 2.45.57 3.57a1 1 0 0 1-.25 1z"/></svg>
    <svg width="16" height="16" viewBox="0 0 24 24" aria-label="Fax"><path fill="#fff" d="M6 3h12v5H6zM4 9h16a2 2 0 0 1 2 2v6h-4v4H6v-4H2v-6a2 2 0 0 1 2-2zm4 7v3h8v-3z"/></svg>
    <svg width="16" height="16" viewBox="0 0 24 24" aria-label="Email"><path fill="#fff" d="M2 5h20v14H2zm2 2v.5l8 5 8-5V7zm0 2.8V17h16V9.8l-8 5z"/></svg>
  </div>

  <ul class="contact">
    <li>(555) 014-2200</li>
    <li>(555) 014-2201</li>
    <li>hello@kestrel-retrofits.com</li>
  </ul>

  <address class="address">
    2410 Harbor Avenue<br>
    Fairview, IL 60999
  </address>

  <div class="footer-band">
    <svg width="700" height="80" viewBox="0 0 700 80">
      <rect x="0" y="18" width="330" height="20" fill="var(--green)"/>
      <rect x="620" y="50" width="80" height="18" fill="var(--green)"/>
      <path d="M300 80 L330 20 Q334 12 344 12 L650 12 L620 80 Z" fill="var(--green-dark)"/>
    </svg>
    <div class="website">www.kestrel-retrofits.com</div>
  </div>
</section>

</body>
</html>
```